Business Card Design for Vintage Jazz

I am a vintage jazz band leader in New York City. My groups play the music of the 1920s, 1930s and 1940s. My website is morvalquist.com for more info on what I do.

I am looking for a two sided business card design that has the look and feel of a really nice business card from the 1930s. I need to convey with the design that my work has that vintage kind of class and style, but also conveys that we are fun and entertaining.

Most importantly it should make a bold staement. If Hal Denbrook had a card, what would it have looked like? I want a card that I feel confident will make an impact and will let people know that my work is te the top that NYC has to offer in vintage jazz..

Note that I have only decided to avoid the "committed payment" option as I have not used this service before. Assuming that I get quality work I will select a design from those presented.

Target Market(s)

people who want to hire my band for events, media, and new fans of the band

Industry/Entity Type

Performing Art

Contact Information for Business Card

Definitely a matte finish, possibly a sort of old style of paper with that brown tint? definitely a thick card.

Requirements
Must have
• FRONT
• My name: Tobin Vashley
• What I do: Bandleader, Guitarist, Vocalist, Songwriter
• Contact Details: morvalquist.com tobin@morvalquist.com 646-555-0148
• BACK
• My Social Media Links:
• facebook.morvalquist.com
• twitter, instagram, linkedin: morvalquist
• I'm also including a photo image I would like to use. The photo's background is not needed, and to be honest isn't really desireable. Just looking to use the image of me.
Nice to have
• I'm attaching which could be used as is, omitted from the card, or altered maybe with text going around the outside of the circle or in some other way. It may need some clean up to the edges of the lettering as we only use it for the website thumbnail.
• If there's space I'd like to include the text "join our mailing list for a free song download: freesong.morvalquist.com" If not perhaps just "Download a Free Song at: freesong.morvalquist.com - something to this end.
Should not have
• anything cartoony. Don't think retro 90s's vision of the swing era, think actual swing era!
• anything modern. Got to look old school
• Try to avoid dark backgrounds. Since we often play in bars and clubs where it is dar, a d
• avoid script fonts.

```html
<!DOCTYPE html>
<html lang="en">
<head>
<meta charset="utf-8">
<title>Tobin Vashley – Business Card</title>
<link rel="stylesheet" href="https://fonts.googleapis.com/css2?family=Arimo:wght@400;700&display=swap">
<style>
  :root {
    --ink: #0b0b0b;
    --paper: #f7f7f5;
    --teal: #6cc4b1;
    --teal-light: #86d3c2;
    --white: #ffffff;
    --stage: #e9e6e1;
    --photo-dark: #3a3a3a;
    --photo-light: #c9c9c9;
  }
  * { box-sizing: border-box; margin: 0; padding: 0; }
  html, body { width: 1200px; height: 864px; overflow: hidden; }
  body {
    background: var(--stage);
    font-family: "Arimo", Arial, sans-serif;
    display: flex;
    flex-direction: column;
    align-items: center;
    justify-content: center;
    gap: 40px;
  }
  .card {
    position: relative;
    width: 630px;
    height: 360px;
    overflow: hidden;
    box-shadow: 0 6px 18px rgba(0,0,0,.18);
  }

  /* FRONT */
  .card-front { background: var(--paper); }
  .front-band {
    position: absolute; left: 0; right: 0; top: 150px; height: 170px;
    background: linear-gradient(90deg, var(--teal), var(--teal-light) 40%, var(--teal));
  }
  .front-base {
    position: absolute; left: 0; right: 0; bottom: 0; height: 40px;
    background: var(--ink);
  }
  .portrait {
    position: absolute; left: 30px; top: 20px; width: 190px; height: 300px;
    background: linear-gradient(180deg, var(--photo-light) 0%, var(--photo-dark) 45%, var(--ink) 100%);
    border-radius: 80px 80px 0 0;
  }
  .identity {
    position: absolute; right: 34px; top: 112px; text-align: right; color: var(--ink);
  }
  .identity .name { font-size: 34px; font-weight: 700; letter-spacing: .5px; line-height: 38px; }
  .identity .role { font-size: 16px; font-weight: 700; margin-top: 4px; white-space: nowrap; }
  .contact {
    position: absolute; right: 34px; top: 222px; list-style: none; color: var(--ink);
    font-size: 18px; line-height: 25px;
  }
  .contact li { display: flex; align-items: center; justify-content: flex-end; gap: 10px; }
  .contact svg { width: 14px; height: 14px; }

  /* BACK */
  .card-back { background: var(--ink); }
  .back-band {
    position: absolute; left: 0; right: 0; bottom: 0; height: 48px;
    background: var(--teal);
  }
  .monogram {
    position: absolute; left: 48px; top: 56px;
    color: var(--white); font-size: 44px; font-weight: 700; letter-spacing: 1px;
  }
  .web-links {
    position: absolute; left: 220px; top: 186px; color: var(--white);
    font-size: 24px; line-height: 38px; white-space: nowrap;
  }
  .web-links .site { padding-left: 20px; }
  .social-top {
    position: absolute; right: 40px; top: 200px; display: flex;
  }
  .social-row {
    position: absolute; right: 40px; top: 244px; display: flex; gap: 12px;
  }
  .social-top span, .social-row span { width: 30px; height: 30px; background: var(--white); display: block; }
</style>
</head>
<body>

  <section class="card card-front" aria-label="Card front">
    <div class="front-band"></div>
    <div class="front-base"></div>
    <div class="portrait" role="img" aria-label="Black and white photo of the bandleader in a blazer tipping a straw boater hat"></div>
    <div class="identity">
      <h1 class="name">Tobin Vashley</h1>
      <p class="role">Bandleader, Guitarist, Vocalist, Songwriter</p>
    </div>
    <ul class="contact">
      <li>646-555-0148
        <svg viewBox="0 0 14 14" aria-hidden="true"><rect width="14" height="14" fill="#0b0b0b"/><path d="M3 5h8v5H3z" fill="none" stroke="#fff" stroke-width="1.4"/></svg></li>
      <li>morvalquist.com
        <svg viewBox="0 0 14 14" aria-hidden="true"><rect width="14" height="14" fill="#0b0b0b"/><circle cx="7" cy="7" r="4" fill="none" stroke="#fff" stroke-width="1.4"/><path d="M3 7h8" stroke="#fff"/></svg></li>
      <li>tobin@morvalquist.com
        <svg viewBox="0 0 14 14" aria-hidden="true"><rect width="14" height="14" fill="#0b0b0b"/><path d="M3 4h8v6H3zM3 4l4 3 4-3" fill="none" stroke="#fff" stroke-width="1.2"/></svg></li>
    </ul>
  </section>

  <section class="card card-back" aria-label="Card back">
    <div class="back-band"></div>
    <p class="monogram">Tobin Vashley</p>
    <div class="web-links">
      <p class="site">morvalquist.com</p>
      <p class="handle">morvalquist</p>
    </div>
    <div class="social-top" aria-label="Social media"><span></span></div>
    <div class="social-row" aria-label="Social media">
      <span></span><span></span><span></span>
    </div>
  </section>

</body>
</html>
```